Schlichtes Design für Malerbetrieb
Zielgruppe
Wir sind ein mittelgroßer Malerbetrieb in München mit umfangreichem Leistungsspektrum.
Unsere Hauptleistungen sind: Fassadenrenovierung, Altbausanierung, Betoninstandsetzung, Balkonabdichtung (kein Neubau!).
Unsere Zielgruppen sind: Hausverwaltungen, Firmen und Privatpersonen.
Unsere Kunden schätzen: Konstruktive Organisation und Planung im Vorfeld, Zuverlässigkeit, saubere Arbeitsweise, dauerhafte Balkonabdichtungen.
Aufgabenstellung
Wir möchten eine langlebige, stilvolle, minimalistische Homepage.
Wir möchten von der bestehenden Homepage nur die Schriftart für unseren Firmennamen (Century Gothic) und wenn möglich (nicht zwingend), irgendwo das florale Muster einbauen. Corporate-Design haben wir nicht.
Farbtöne: Firmennamen Orange (hellorange bis erdiges Orange möglich, da sind wir nicht fixiert) , einen dunklen Hintergrundfarbton (Petrol-Blaugrau ?) mit gelbem (neon bis senfgelb) Akzent (Linien), Blumenmuster weiß, grau.
Dies sind nur unsere Ideen. Wir sind aber auch absolut offen für eure Profi-Ideen.
Wir möchten uns von den unzähligen langweiligen 'Pinselseiten mit veralteten Bilder' unserer Kollegen interessant und mit Stil abheben.
Eher nach dem Motto 'weniger ist mehr'.
Einen positiven, sympathischen Eindruck geben und unsere Leistungen in den Vordergrund bringen.
Da wir viele Stammkunden haben, betreiben wir kein Social-Media und möchten dies vorerst auch nicht tun.
Die Seite wird in den nächsten Jahren nicht verändert, höchstens die Bilder aktualisiert.
Die Texte haben wir alle selbst entworfen und möchten wir so übernehmen.
Die Galerien sollen unkompliziert anzuschauen sein.
Uns gefällt die Struktur und Schlichtheit von https://vaartmolen.nl/ oder Timbra.de gut und wir mögen Vintage-Grafiken gerne.
Einerseits darf die Seite geradlinig, andererseits aber auch rund und floral wirken.

```html
<!DOCTYPE html>
<html lang="de">
<head>
<meta charset="utf-8">
<title>kolbrit Malerarbeiten</title>
<link rel="stylesheet" href="https://fonts.googleapis.com/css2?family=Questrial&family=Oswald:wght@300;400&display=swap">
<style>
  :root{
    --bar:#404040;
    --stage:#434343;
    --pattern:#4a4a4a;
    --navy:#34325a;
    --amber:#f7b234;
    --muted:#6e6e72;
    --white:#ffffff;
  }
  html,body{margin:0;padding:0;width:1200px;height:900px;overflow:hidden;background:var(--stage);}
  .page{position:relative;width:1200px;height:900px;overflow:hidden;}
  .header{position:absolute;left:0;top:0;width:1200px;height:129px;background:var(--bar);}
  .brand{position:absolute;right:26px;top:18px;margin:0;font-family:"Questrial",sans-serif;font-weight:400;font-size:50px;line-height:1;color:var(--amber);letter-spacing:1px;}
  .nav{position:absolute;right:22px;top:88px;display:flex;gap:18px;font-family:"Oswald",sans-serif;font-weight:300;font-size:21px;letter-spacing:0.6px;color:var(--white);text-transform:uppercase;}
  .nav a,.footer a{color:inherit;text-decoration:none;}
  .stage{position:absolute;left:0;top:129px;width:1200px;height:714px;}
  .stage svg{display:block;}
  .hero-mark{position:absolute;left:116px;top:340px;margin:0;font-family:"Questrial",sans-serif;font-weight:400;font-size:104px;line-height:1;color:var(--amber);letter-spacing:2px;}
  .hero-sub{position:absolute;left:188px;top:452px;margin:0;font-family:"Questrial",sans-serif;font-size:22px;letter-spacing:6.2px;color:var(--muted);}
  .footer{position:absolute;left:0;top:843px;width:1200px;height:57px;background:var(--bar);}
  .footer nav{position:absolute;right:26px;top:14px;display:flex;gap:16px;font-family:"Oswald",sans-serif;font-weight:400;font-size:20px;color:var(--white);text-transform:uppercase;}
</style>
</head>
<body>
<div class="page">
  <header class="header">
    <p class="brand">kolbrit</p>
    <nav class="nav">
      <a href="#">Malerarbeiten</a>
      <a href="#">Betoninstandsetzung</a>
      <a href="#">Balkonabdichtung</a>
      <a href="#">Farbgestaltung</a>
      <a href="#">Wärmedämmung</a>
      <a href="#">Ausbildung</a>
      <a href="#">Portrait</a>
    </nav>
  </header>

  <section class="stage">
    <svg width="1200" height="714" viewBox="0 0 1200 714">
      <defs>
        <linearGradient id="patternTone" x1="0" y1="0" x2="1" y2="1">
          <stop offset="0" stop-color="#4c4c4c"/>
          <stop offset="1" stop-color="#444444"/>
        </linearGradient>
        <linearGradient id="photoTone" x1="0" y1="0" x2="0" y2="1">
          <stop offset="0" stop-color="#8a8680"/>
          <stop offset="0.35" stop-color="#d9c9a3"/>
          <stop offset="1" stop-color="#b8a98a"/>
        </linearGradient>
      </defs>
      <rect width="1200" height="714" fill="var(--stage)"/>
      <polygon role="img" aria-label="Florales Damastmuster in Grautönen" points="264,0 1200,0 1200,322 855,293" fill="url(#patternTone)"/>
      <polygon role="img" aria-label="Foto eines historischen Stadtgebäudes mit heller Fassade" points="674,387 1200,639 1200,714 316,714 316,572" fill="url(#photoTone)"/>
      <polygon class="navy-band" points="0,0 264,0 855,293 0,735" fill="var(--navy)"/>
      <polygon class="amber-wedge" points="0,396 650,714 0,714" fill="var(--amber)"/>
    </svg>
  </section>

  <h1 class="hero-mark">kolbrit</h1>
  <p class="hero-sub">MALERARBEITEN</p>

  <footer class="footer">
    <nav>
      <a href="#">Kontakt</a>
      <a href="#">Impressum</a>
      <a href="#">Datenschutz</a>
    </nav>
  </footer>
</div>
</body>
</html>
```